BRELDON ELECTRICAL

all black background with silver and lime writing, fonts i like are gothic style but am open to ideas, will need a picture logo aswell as im putting this on my van.i am a electrical contractor starting up my own electrical business. underneath breldon electrical heading on card we could put" professiona cost effective soloutions to all your electrical needs".{ or something of that nature }.on aback of card on top half list servises provided, real estate and commercial maintenance, new home and renovation rewires and upgrades, split system air conditioning, floor heat, tv phone data, smoke detoctors, lighting systems , builders welcome, , and also a thankyou for your business.

Contact Information for Business Card

GARETH PILKSWORTH
breldonelectrical@quivmail.com.au
0413927154
lic no 58190
ac lic no l263917
abn 31726458103

```html
<!DOCTYPE html>
<html lang="en">
<head>
<meta charset="utf-8">
<title>Breldon Electrical – Business Cards</title>
<link rel="stylesheet" href="https://fonts.googleapis.com/css2?family=Open+Sans:wght@400;600&display=swap">
<style>
  :root {
    --backdrop: #d4d4d4;
    --card-black: #050505;
    --lime: #8ac926;
    --lime-band: #86c22a;
    --silver: #9a9a9a;
    --strip-grey: #4a4a4a;
    --ink-dark: #111111;
  }
  * { box-sizing: border-box; margin: 0; padding: 0; }
  html, body {
    width: 1200px;
    height: 1000px;
    overflow: hidden;
    background: var(--backdrop);
    font-family: "Open Sans", Arial, sans-serif;
  }
  .canvas {
    position: relative;
    width: 1200px;
    height: 1000px;
  }
  .card {
    position: absolute;
    width: 760px;
    height: 420px;
    background: var(--card-black);
    overflow: hidden;
    box-shadow: 0 6px 18px rgba(0,0,0,0.25);
  }
  .card--back { left: 60px; top: 50px; }
  .card--front { left: 60px; top: 520px; }

  /* Brand lockup: name text plus tagline */
  .brand {
    position: absolute;
    text-align: center;
  }
  .brand__dot {
    display: block;
    margin: 0 auto 14px;
    width: 86px;
    height: 86px;
    border-radius: 50%;
    background: var(--lime);
  }
  .brand__name {
    display: block;
    font-weight: 400;
    font-size: 27px;
    letter-spacing: 1.5px;
    color: var(--lime);
    white-space: nowrap;
  }
  .brand__tagline {
    display: block;
    margin-top: 3px;
    font-weight: 600;
    font-size: 10px;
    letter-spacing: 0.2px;
    color: var(--silver);
    white-space: nowrap;
  }

  /* Back: list of services */
  .services {
    position: absolute;
    left: 48px;
    top: 40px;
    list-style: none;
    font-size: 20px;
    line-height: 1.12;
    color: var(--lime);
  }
  .card--back .brand { right: 36px; bottom: 40px; }

  /* Front: contact details */
  .contact {
    position: absolute;
    left: 60px;
    top: 120px;
    color: var(--lime);
    font-size: 22px;
    line-height: 1.2;
  }
  .contact__name {
    font-size: 27px;
    letter-spacing: 0.5px;
  }
  .contact__phone { margin-bottom: 20px; }
  .card--front .brand { right: 70px; top: 80px; }

  .contact-strip {
    position: absolute;
    left: 0;
    bottom: 80px;
    width: 100%;
    height: 10px;
    background: var(--strip-grey);
  }
  .email-band {
    position: absolute;
    left: 0;
    bottom: 0;
    width: 100%;
    height: 80px;
    background: var(--lime-band);
    display: flex;
    align-items: center;
    justify-content: center;
    font-size: 26px;
    color: var(--ink-dark);
  }

  /* Stand-alone brand tile */
  .brand-tile {
    position: absolute;
    left: 880px;
    top: 700px;
    width: 280px;
    height: 240px;
    background: var(--card-black);
  }
  .brand-tile .brand {
    left: 0;
    right: 0;
    top: 34px;
  }
  .brand-tile .brand__name { font-size: 22px; }
  .brand-tile .brand__tagline { font-size: 8px; }
</style>
</head>
<body>
<main class="canvas">

  <section class="card card--back" aria-label="Business card back">
    <ul class="services">
      <li>Real Estate and Commercial Maintenance</li>
      <li>New Home and Renovation Rewires and Upgrades</li>
      <li>Split System Air Conditioning</li>
      <li>Floor Heat</li>
      <li>TV Phone Data</li>
      <li>Smoke Detectors</li>
      <li>Lighting Systems</li>
      <li>Builders Welcome</li>
    </ul>
    <div class="brand">
      <span class="brand__dot"></span>
      <span class="brand__name">BRELDON ELECTRICAL</span>
      <span class="brand__tagline">Reliable, affordable electrical work for every home and business</span>
    </div>
  </section>

  <section class="card card--front" aria-label="Business card front">
    <div class="contact">
      <p class="contact__name">GARETH PILKSWORTH</p>
      <p class="contact__phone">+ 0413927154</p>
      <p>LIC No : 58190</p>
      <p>AC LIC No : l263917</p>
      <p>ABN : 31726458103</p>
    </div>
    <div class="brand">
      <span class="brand__dot"></span>
      <span class="brand__name">BRELDON ELECTRICAL</span>
      <span class="brand__tagline">Reliable, affordable electrical work for every home and business</span>
    </div>
    <div class="contact-strip"></div>
    <div class="email-band">breldonelectrical@quivmail.com.au</div>
  </section>

  <section class="brand-tile" aria-label="Brand tile">
    <div class="brand">
      <span class="brand__dot"></span>
      <span class="brand__name">BRELDON ELECTRICAL</span>
      <span class="brand__tagline">Reliable, affordable electrical work for every home and business</span>
    </div>
  </section>

</main>
</body>
</html>
```